Need help in designing new business card utilizing our new logo.

BuildMark Solutions works with Construction Business Owners, Managers & IT Professionals to strengthen software usage and increase user productivity.

Our Construction Accounting and Mobile Field Management Software Clients engage with us in the following areas:

New Software Implementations
Software Re-Implementations
Redesigning Software Usage at the User Level
Project Coordination & Management
Continued Software Support

Old tag line:
Evaluating Systems - Delivering Results

www.buildmark-solutions.example

Ridge 4 is a product, but not needed for a new business card.

```html
<!DOCTYPE html>
<html lang="en">
<head>
<meta charset="utf-8">
<title>BuildMark Solutions – Business Card</title>
<link rel="stylesheet" href="https://fonts.googleapis.com/css2?family=Arimo:wght@400;700&family=Montserrat:wght@400;600;700&display=swap">
<style>
  :root {
    --brand-blue: #2e3192;
    --brand-grey: #a7a9ac;
    --light-grey: #c9cacc;
    --text-blue: #2b2f8f;
    --card-white: #ffffff;
    --backdrop: #e7e3dd;
  }
  * { margin: 0; padding: 0; box-sizing: border-box; }
  html, body { width: 900px; height: 1200px; overflow: hidden; }
  body { background: var(--backdrop); position: relative; font-family: "Arimo", Arial, sans-serif; }

  .card {
    position: absolute; left: 88px; width: 732px; height: 428px;
    background: var(--card-white); border-radius: 22px; overflow: hidden;
    box-shadow: 0 6px 18px rgba(0,0,0,0.18);
  }
  .card--front { top: 126px; }
  .card--back { top: 640px; }

  /* Front */
  .front-brand {
    position: absolute; left: 86px; top: 168px; width: 210px;
    display: flex; align-items: center; gap: 10px;
    font-family: "Montserrat", sans-serif; font-weight: 700; font-size: 21px;
    color: var(--brand-blue); line-height: 1.15;
  }
  .brand-square { width: 26px; height: 26px; background: var(--brand-blue); flex: none; }
  .divider { position: absolute; width: 2px; background: var(--brand-blue); }
  .front-divider { left: 316px; top: 124px; height: 168px; }
  .contact { position: absolute; left: 357px; top: 120px; color: var(--text-blue); }
  .contact-name { font-size: 22px; letter-spacing: 0.5px; font-weight: 400; text-transform: uppercase; }
  .contact-name strong { font-weight: 700; }
  .contact-role { font-size: 15px; color: var(--brand-grey); letter-spacing: 0.5px; margin-top: 2px; }
  .contact-address { font-size: 16px; line-height: 22px; margin-top: 12px; }
  .contact-lines { list-style: none; margin-top: 12px; font-size: 16px; line-height: 22.5px; }
  .contact-lines li { display: flex; align-items: center; gap: 8px; }
  .contact-lines svg { width: 13px; height: 13px; fill: var(--text-blue); flex: none; }
  .front-band {
    position: absolute; left: 0; right: 0; top: 371px; height: 38px;
    background: var(--brand-blue); color: #fff;
    font-family: "Montserrat", sans-serif; font-weight: 600; font-size: 15.5px;
    display: flex; align-items: center; justify-content: center; letter-spacing: 0.3px;
  }

  /* Back */
  .back-brand {
    position: absolute; left: 0; right: 0; top: 165px;
    display: flex; align-items: center; justify-content: center; gap: 18px;
    font-family: "Montserrat", sans-serif; font-weight: 700; font-size: 50px;
    color: var(--brand-blue);
  }
  .back-brand .brand-square { width: 58px; height: 58px; }
  .website {
    position: absolute; left: 0; right: 0; top: 354px; text-align: center;
    font-family: "Montserrat", sans-serif; font-weight: 700; font-size: 15px;
    letter-spacing: 8.5px; color: var(--brand-blue);
  }
  .back-band {
    position: absolute; left: 0; right: 0; top: 387px; height: 41px;
    background: var(--brand-blue);
  }
  .back-band-corner { position: absolute; left: 0; top: 387px; width: 100px; height: 41px; }
  .tagline {
    position: absolute; left: 80px; right: 0; top: 387px; height: 41px;
    display: flex; align-items: center; justify-content: center;
    font-family: "Montserrat", sans-serif; font-weight: 400; font-size: 20.5px; color: #fff;
    white-space: nowrap;
  }
  .tagline strong { font-weight: 700; }
</style>
</head>
<body>

  <section class="card card--front">
    <div class="front-brand"><span class="brand-square"></span><span>BuildMark Solutions</span></div>
    <div class="divider front-divider"></div>
    <div class="contact">
      <p class="contact-name"><strong>Dana R.</strong> Hale</p>
      <p class="contact-role">OWNER</p>
      <p class="contact-address">48B Harbor Lane- PMB 112<br>Millbrook NY 12545</p>
      <ul class="contact-lines">
        <li><svg viewBox="0 0 16 16" aria-hidden="true"><path d="M3.6 1.2 6 3.8 4.8 5.8c.9 2.1 2.9 4.2 5.3 5.3l2-1.3 2.7 2.4-1.4 2.4C7.7 14.6 1.4 8.4 1.2 2.6z"/></svg>800-555-0142 ext.100</li>
        <li><svg viewBox="0 0 16 16" aria-hidden="true"><path d="M4 0h8a1 1 0 0 1 1 1v14a1 1 0 0 1-1 1H4a1 1 0 0 1-1-1V1a1 1 0 0 1 1-1zm1 2v10h6V2zm3 11a1 1 0 1 0 0 2 1 1 0 0 0 0-2z"/></svg>518-555-0173</li>
        <li><svg viewBox="0 0 16 16" aria-hidden="true"><path d="M0 3h16v10H0zm1.5 1.3v.4L8 9l6.5-4.3v-.4z"/></svg>dana.hale@buildmark-solutions.example</li>
      </ul>
    </div>
    <div class="front-band">CONSTRUCTION ACCOUNTING SOFTWARE CONSULTANTS</div>
  </section>

  <section class="card card--back">
    <div class="back-brand"><span class="brand-square"></span><span>BuildMark Solutions</span></div>
    <p class="website">WWW.BUILDMARK-SOLUTIONS.EXAMPLE</p>
    <div class="back-band"></div>
    <svg class="back-band-corner" viewBox="0 0 100 41" aria-hidden="true"><polygon points="0,0 48,0 96,41 0,41" fill="var(--light-grey)"/></svg>
    <p class="tagline"><span><strong>EVALUATING</strong> SYSTEMS – <strong>DELIVERING</strong> RESULTS</span></p>
  </section>

</body>
</html>
```